Vale Linebacker Needs a new website!

We need a four page website for a new company based in San Francisco. We help companies connect better with their clients, employees, and vendors by implementing collaborative technology.
Similar Websites
Mist Rangers - http://www.mistrangers.example/
Skyforthing - http://www.skyforthing.example/ - I don't like the the rotating window or the pictures of people. I like the icons used to go to the next pages.
Color Combos
Blues and Yellows - http://www.huepairings.example/palette-sets/96/HuePairing96.html
We prefer graphics over the actual pictures of people in the header. Pictures of people working together in the text is fine.
Web Page Layout
Index
Cloud Advisory Services
Email Everywhere
CRM Implementation
For detailed copy please see this link https://files.paperhold.example/a/widgetladyla.example/document/d/7KtmPzWqAeRbYcNvHsJgLdFxTuQoIeMnBvCxZaSdFgHj/edit
Industry/Entity Type
It Company

```html
<!DOCTYPE html>
<html lang="en">
<head>
<meta charset="utf-8">
<title>Vale Linebacker</title>
<link rel="stylesheet" href="https://fonts.googleapis.com/css2?family=Roboto:ital,wght@0,400;0,500;0,700;1,400&family=Open+Sans:wght@400;600&display=swap">
<style>
:root{
  --blue:#2160b4;
  --blue-dark:#1a4f98;
  --blue-deep:#17467f;
  --yellow:#f3c21b;
  --ink:#333;
  --muted:#777;
  --grey-band:#e6e9ee;
  --footer:#333333;
  --footer-bar:#272727;
  --white:#fff;
}
*{box-sizing:border-box;margin:0;padding:0}
html,body{width:1200px;height:2359px;overflow:hidden}
body{font-family:"Open Sans",Arial,sans-serif;color:var(--ink);background:var(--white);font-size:12px;position:relative}
.section{position:absolute;left:0;width:1200px}
h2.section-title{font-family:"Roboto",Arial,sans-serif;font-weight:400;color:var(--blue);font-size:19px;text-align:center}

/* hero */
.hero{top:0;height:653px;background:linear-gradient(120deg,#cfdbe6 0%,#9fb6c9 35%,#5d7590 65%,#2b3a4f 100%)}
.hero-art{position:absolute;inset:0}
.hero-line{position:absolute;left:0;top:648px;width:1200px;height:5px;background:var(--blue)}
.masthead{position:absolute;left:171px;top:16px;width:859px;height:114px;background:var(--white);box-shadow:0 1px 3px rgba(0,0,0,.25)}
.brand{position:absolute;left:14px;top:38px;display:flex;align-items:center;gap:10px}
.brand-dot{width:34px;height:34px;border-radius:50%;background:var(--blue)}
.brand-name{font-family:"Roboto",Arial,sans-serif;font-weight:700;font-size:30px;color:var(--blue)}
.search{position:absolute;right:10px;top:54px;width:274px;height:40px;border:1px solid #ddd;font-size:10px;color:#aaa;padding:12px 10px}
.search svg{position:absolute;right:12px;top:13px}
.nav{position:absolute;left:171px;top:130px;width:859px;height:54px;background:linear-gradient(#2467c0,#1c56a6);display:flex;align-items:center;padding-left:10px}
.nav a{color:var(--white);text-decoration:none;font-size:12.5px;padding:0 18px;height:54px;line-height:54px;border-right:1px solid rgba(255,255,255,.15)}
.nav a:first-child{color:var(--yellow)}
.nav a:nth-child(1){width:82px}
.nav a:nth-child(n+2){width:98px;text-align:center}
.nav a:last-child{border-right:none;width:120px}
.caption{position:absolute;left:181px;top:374px}
.caption h1{font-family:"Roboto",Arial,sans-serif;font-weight:400;font-size:26px;color:#111}
.caption p{font-size:12.5px;color:#111;margin-top:10px}
.arrow{position:absolute;top:338px;width:34px;height:34px;border-radius:50%;background:rgba(60,60,60,.7)}
.arrow svg{position:absolute;left:10px;top:9px}

/* feature cards */
.features{position:absolute;left:181px;top:554px;width:838px;display:flex;justify-content:space-between}
.feature{width:266px;text-align:center}
.feature-head{height:102px;background:var(--white);border-top:5px solid var(--blue);padding-top:30px}
.feature-art{width:100px;height:90px;margin:0 auto;border-radius:12px}
.feature h3{font-family:"Roboto",Arial,sans-serif;font-weight:400;color:var(--blue);font-size:16px;margin-top:52px}
.feature p{font-size:11.2px;line-height:19px;color:#444;margin-top:6px;padding:0 10px}
.divider{position:absolute;left:171px;top:850px;width:859px;border-top:1px dashed #ccc}
.welcome{top:870px;text-align:center}
.welcome p{width:860px;margin:14px auto 0;font-size:11.2px;line-height:19px;color:#444}

/* what we do */
.what{top:958px;height:465px;background:var(--grey-band);border-top:1px solid #dde}
.what h2{margin-top:20px}
.what .lead{width:860px;margin:10px auto 0;text-align:center;font-size:11.2px;line-height:19px;color:#444}
.services{position:absolute;left:181px;top:99px;width:838px;height:343px;background:var(--white);border:1px solid #d6d9de;border-radius:4px;display:grid;grid-template-columns:1fr 1fr;grid-auto-rows:108px;padding:20px 0 0 44px}
.service{display:flex;gap:14px}
.service svg{flex:none}
.service h3{font-family:"Roboto",Arial,sans-serif;font-weight:400;color:var(--blue);font-size:15px;margin-top:4px}
.service p{font-size:10.5px;line-height:18px;color:#555;width:275px;margin-top:2px}

/* posts */
.posts{top:1423px;height:365px}
.posts h2{margin-top:28px}
.post-row{position:absolute;left:181px;top:74px;width:838px;display:flex;justify-content:space-between}
.post{width:195px;height:249px;background:#f4f5f8;box-shadow:0 4px 5px rgba(0,0,0,.18)}
.post-img{height:134px}
.post h4{font-family:"Roboto",Arial,sans-serif;font-weight:400;font-size:12.5px;line-height:17px;color:#222;padding:10px 12px 0}
.post p{font-size:9.5px;line-height:14px;color:#999;padding:6px 12px 0}
.read-more{display:flex;justify-content:flex-end;align-items:center;gap:4px;padding:8px 12px 0;font-size:10px;font-style:italic;color:var(--blue)}
.read-more i{width:8px;height:8px;border-radius:50%;background:var(--yellow)}

/* testimonials */
.clients{top:1788px;height:239px;background:var(--blue)}
.clients h2{color:var(--white);margin-top:26px;font-size:19px}
.quote{position:absolute;top:73px;width:330px;height:134px;background:var(--blue-deep);border-radius:3px;padding:10px 12px 0 40px;font-size:10px;line-height:16px;color:var(--white)}
.quote-photo{position:absolute;z-index:1;top:91px;width:97px;height:97px;border:5px solid var(--yellow);background:linear-gradient(#a9b4bf,#7a8591)}
.quote .author{color:var(--yellow)}
.quote .more{color:var(--yellow)}

/* client logos */
.logos{top:2027px;height:115px;display:flex;justify-content:space-between;align-items:center;padding:0 178px 0 183px}
.logo{display:flex;align-items:center;gap:6px;font-family:"Roboto",Arial,sans-serif;font-size:17px;color:#9a9a9a}
.logo i{width:14px;height:14px;background:#9a9a9a;border-radius:50%}

/* footer */
.footer{top:2142px;height:164px;background:var(--footer);color:#ddd}
.footer-col{position:absolute;top:26px}
.footer-col h5{font-family:"Roboto",Arial,sans-serif;font-style:italic;font-weight:400;font-size:15px;color:var(--white)}
.footer-col ul{list-style:none;margin:8px 0 0 25px}
.footer-col li{font-size:11px;line-height:26px}
.social li{display:flex;align-items:center;gap:6px}
.social li i{width:10px;height:10px;background:#4a79c7;border-radius:2px}
.social li.rss i{background:#f08a24}
.contact li{display:flex;gap:8px;line-height:17px;margin-bottom:12px}
.contact svg{flex:none;margin-top:2px}
.bottom-bar{top:2306px;height:53px;background:var(--footer-bar);color:#ccc;font-size:10px}
.bottom-bar .left{position:absolute;left:181px;top:21px}
.bottom-bar .right{position:absolute;right:181px;top:21px}
</style>
</head>
<body>

<section class="section hero">
  <div class="hero-art" role="img" aria-label="Photo of a businessman touching a glowing cloud network diagram"></div>
  <div class="hero-line"></div>
  <header class="masthead">
    <div class="brand"><span class="brand-dot"></span><span class="brand-name">Vale Linebacker</span></div>
    <div class="search">Search...
      <svg width="12" height="12" viewBox="0 0 12 12"><circle cx="5" cy="5" r="3.8" fill="none" stroke="#bbb" stroke-width="1.4"/><line x1="8" y1="8" x2="11" y2="11" stroke="#bbb" stroke-width="1.4"/></svg>
    </div>
  </header>
  <nav class="nav">
    <a>Home</a><a>Services</a><a>Company</a><a>Partners</a><a>Events</a><a>Resources</a><a>Blog</a><a>Contact Us</a>
  </nav>
  <div class="arrow" style="left:14px"><svg width="14" height="16" viewBox="0 0 14 16"><path d="M10 2 L4 8 L10 14" fill="none" stroke="#fff" stroke-width="2.5"/></svg></div>
  <div class="arrow" style="left:1148px"><svg width="14" height="16" viewBox="0 0 14 16"><path d="M4 2 L10 8 L4 14" fill="none" stroke="#fff" stroke-width="2.5"/></svg></div>
  <div class="caption">
    <h1>Lorem ipsum dolor sit amet</h1>
    <p>Typi non habent claritatem insitam; est usus legentis in iis qui facit</p>
  </div>
  <div class="features">
    <div class="feature">
      <div class="feature-head"><div class="feature-art" role="img" aria-label="Blue cloud illustration" style="background:linear-gradient(#8fd0f5,#2a8ad6)"></div></div>
      <h3>Cloud Advisory</h3>
      <p>Forward- thinking organizations would like to be more collaborative, flexible and productive. Put your cloud program on the path to success with our Advisory Services.</p>
    </div>
    <div class="feature">
      <div class="feature-head"><div class="feature-art" role="img" aria-label="Envelope with a blue globe illustration" style="background:linear-gradient(#f2f4f6,#b9c2cc)"></div></div>
      <h3>Email Everywhere</h3>
      <p>Drive forward your business with innovative solutions for the enterprise with either Docmesh Suite or Deskline 365. Experience improved collaboration, security, mobility while increasing your overall IT investment.</p>
    </div>
    <div class="feature">
      <div class="feature-head"><div class="feature-art" role="img" aria-label="Stacked database disks illustration" style="background:linear-gradient(#c9ccd0,#e0a54a 45%,#3a7bc8 75%,#8a8f96)"></div></div>
      <h3>CRM Solutions</h3>
      <p>CRMs (Customer Relationship Management) can be complex and slow for employees to adopt. Accelerate your CRM adoption by selecting the right simple solution for your business.</p>
    </div>
  </div>
</section>

<div class="divider"></div>
<section class="section welcome">
  <h2 class="section-title">Welcome To Vale Linebacker</h2>
  <p>Lorem ipsum dolor sit amet, consectetuer adipiscing elit, sed diam nonummy nibh euismod tincidunt ut laoreet dolore magna aliquam erat volutpat. Ut wisi enim ad minim veniam, quis nostrud exerci tation ullamcorper suscipit lobortis nisl ut aliquip ex ea commodo consequat.</p>
</section>

<section class="section what">
  <h2 class="section-title">What We Do</h2>
  <p class="lead">We challenge the status quo by providing unique insights, emerging strategies and proven best practices. Our unwavering focus is on customer satisfaction. Our services include:</p>
  <div class="services">
    <div class="service">
      <svg width="70" height="66" viewBox="0 0 70 66"><rect x="6" y="4" width="58" height="40" fill="none" stroke="#111" stroke-width="5"/><polyline points="18,32 30,20 40,28 52,14" fill="none" stroke="#111" stroke-width="3"/><line x1="20" y1="44" x2="14" y2="64" stroke="#111" stroke-width="5"/><line x1="50" y1="44" x2="56" y2="64" stroke="#111" stroke-width="5"/></svg>
      <div><h3>Strategy</h3><p>Typi non habent claritatem insitam; est usus legentis in iis qui facit eorum claritatem.</p></div>
    </div>
    <div class="service">
      <svg width="70" height="66" viewBox="0 0 70 66"><path d="M24 14a8 8 0 0 1 14-6a7 7 0 0 1 12 5a5 5 0 0 1 0 10H26a5 5 0 0 1-2-9z" fill="none" stroke="#111" stroke-width="3"/><g fill="#111"><circle cx="14" cy="34" r="5"/><rect x="8" y="40" width="12" height="24"/><circle cx="35" cy="32" r="5"/><rect x="29" y="38" width="12" height="26"/><circle cx="56" cy="34" r="5"/><rect x="50" y="40" width="12" height="24"/></g></svg>
      <div><h3>Migration</h3><p>Typi non habent claritatem insitam; est usus legentis in iis qui facit eorum claritatem.</p></div>
    </div>
    <div class="service">
      <svg width="70" height="66" viewBox="0 0 70 66"><path d="M26 22a9 9 0 0 1 16-6a7 7 0 0 1 8 10H26z" fill="#111"/><path d="M6 52a7 7 0 0 1 12-5a6 6 0 0 1 8 8H6z" fill="#111"/><path d="M42 52a7 7 0 0 1 12-5a6 6 0 0 1 8 8H42z" fill="#111"/><line x1="20" y1="44" x2="20" y2="34" stroke="#111" stroke-width="3"/><line x1="50" y1="44" x2="50" y2="34" stroke="#111" stroke-width="3"/><line x1="20" y1="34" x2="50" y2="34" stroke="#111" stroke-width="3"/><line x1="35" y1="26" x2="35" y2="34" stroke="#111" stroke-width="3"/></svg>
      <div><h3>Implementation</h3><p>Typi non habent claritatem insitam; est usus legentis in iis qui facit eorum claritatem.</p></div>
    </div>
    <div class="service">
      <svg width="70" height="66" viewBox="0 0 70 66"><g fill="#111"><polygon points="6,6 28,28 28,14 20,14"/><polygon points="64,6 42,28 56,28 56,20"/><polygon points="6,62 28,40 28,54 20,54"/><polygon points="64,62 42,40 56,40 56,48"/></g><g stroke="#111" stroke-width="6"><line x1="8" y1="8" x2="26" y2="26"/><line x1="62" y1="8" x2="44" y2="26"/><line x1="8" y1="60" x2="26" y2="42"/><line x1="62" y1="60" x2="44" y2="42"/></g></svg>
      <div><h3>Integration</h3><p>Typi non habent claritatem insitam; est usus legentis in iis qui facit eorum claritatem.</p></div>
    </div>
    <div class="service">
      <svg width="70" height="66" viewBox="0 0 70 66"><path d="M16 50a10 10 0 0 1 2-20a16 16 0 0 1 30-6a12 12 0 0 1 8 26z" fill="#111"/><path d="M36 30v14M29 37h14" stroke="#fff" stroke-width="4"/></svg>
      <div><h3>Adoption</h3><p>Typi non habent claritatem insitam; est usus legentis in iis qui facit eorum claritatem.</p></div>
    </div>
    <div class="service">
      <svg width="70" height="66" viewBox="0 0 70 66"><g fill="#111"><ellipse cx="22" cy="10" rx="16" ry="5"/><rect x="6" y="14" width="32" height="12"/><rect x="6" y="30" width="32" height="12"/><rect x="6" y="46" width="32" height="14"/></g><path d="M50 12h10v44H50" fill="none" stroke="#111" stroke-width="3"/><polygon points="55,26 60,32 55,38 50,32" fill="#111"/></svg>
      <div><h3>Change Management</h3><p>Typi non habent claritatem insitam; est usus legentis in iis qui facit eorum claritatem.</p></div>
    </div>
  </div>
</section>

<section class="section posts">
  <h2 class="section-title">Our Recent Posts</h2>
  <div class="post-row">
    <article class="post">
      <div class="post-img" role="img" aria-label="Photo of glowing fibre optic cables" style="background:linear-gradient(#0d2a55,#2a6fc4)"></div>
      <h4>Claritas est etiam processus dynamicus, qui sequitur</h4>
      <p>Claritas est etiam processus dyna icus, qui sequitur mutationem consuetudium...</p>
      <div class="read-more">Read More <i></i></div>
    </article>
    <article class="post">
      <div class="post-img" role="img" aria-label="Photo of a hand touching digital app icons beside a phone" style="background:linear-gradient(#0a2440,#3d86c6)"></div>
      <h4>Typi non habent claritatem insitam; est usus legentis</h4>
      <p>Claritas est etiam processus dyna icus, qui sequitur mutationem consuetudium...</p>
      <div class="read-more">Read More <i></i></div>
    </article>
    <article class="post">
      <div class="post-img" role="img" aria-label="Photo of a close-up circuit board" style="background:linear-gradient(#0b1a24,#3f6d6a)"></div>
      <h4>Nam liber tempor cum soluta nobis eleifend</h4>
      <p>Claritas est etiam processus dyna icus, qui sequitur mutationem consuetudium...</p>
      <div class="read-more">Read More <i></i></div>
    </article>
    <article class="post">
      <div class="post-img" role="img" aria-label="Photo of an office desk with computers" style="background:linear-gradient(#b8c7d4,#3b5d80)"></div>
      <h4>Ut wisi enim ad minim quis nostrud exerci</h4>
      <p>Claritas est etiam processus dyna icus, qui sequitur mutationem consuetudium...</p>
      <div class="read-more">Read More <i></i></div>
    </article>
  </div>
</section>

<section class="section clients">
  <h2 class="section-title">What our clients are saying?</h2>
  <div class="quote-photo" role="img" aria-label="Portrait of a client" style="left:185px"></div>
  <div class="quote" style="left:251px">T services consultant and infrastructure architect with a strong background in a wide range of IT infrastructure and application development exposure. Most effective designing and managing infrastructure and IT services in startups, high tech companies, and companies undergoing growth and structural change.<br><span class="author">-JR Halden</span></div>
  <div class="quote-photo" role="img" aria-label="Portrait of a client" style="left:618px"></div>
  <div class="quote" style="left:684px">Deep experienced in delivering a wide variety of IT business applications on time and within budget from very large to very small companies. Seeing hyper-growth operations as well as streamlining steady business practices in the financial services, communications, media, retail industries, I have managed implementations and daily operations for internal and..... <span class="more">Read More</span></div>
</section>

<section class="section logos">
  <div class="logo"><i></i>Business</div>
  <div class="logo"><i></i>Your Logo</div>
  <div class="logo"><i></i>Business</div>
  <div class="logo"><i></i>Brand</div>
  <div class="logo"><i></i>Designer</div>
  <div class="logo"><i></i>Logo</div>
</section>

<footer class="section footer">
  <div class="footer-col" style="left:183px">
    <h5>Quick Links</h5>
    <ul><li>Home</li><li>About Us</li><li>Services</li><li>Contact Us</li></ul>
  </div>
  <div class="footer-col" style="left:398px">
    <h5>Help &amp; Support</h5>
    <ul><li>FAQ's</li><li>Live Support</li><li>Send Mail</li></ul>
  </div>
  <div class="footer-col social" style="left:602px">
    <h5>Social Connection</h5>
    <ul><li><i></i>Friendwall</li><li><i></i>Chirpline</li><li><i></i>Circlespace</li><li class="rss"><i></i>RSS</li></ul>
  </div>
  <div class="footer-col contact" style="left:808px">
    <h5>Get In touch</h5>
    <ul>
      <li><svg width="10" height="10" viewBox="0 0 10 10"><path d="M2 0l2 3-1 1a6 6 0 0 0 3 3l1-1 3 2-1 2C4 10 0 6 0 2z" fill="#ddd"/></svg>+(10)-55-010-200-4</li>
      <li><svg width="12" height="9" viewBox="0 0 12 9"><rect x=".5" y=".5" width="11" height="8" fill="none" stroke="#ddd"/><path d="M.5 .5 6 5l5.5-4.5" fill="none" stroke="#ddd"/></svg>hello@valelinebacker.example</li>
      <li><svg width="9" height="12" viewBox="0 0 9 12"><path d="M4.5 12S0 6.5 0 4.5a4.5 4.5 0 0 1 9 0C9 6.5 4.5 12 4.5 12z" fill="#ddd"/><circle cx="4.5" cy="4.5" r="1.6" fill="#333"/></svg>38 lorem ipsm2 rd, lorem ipsm,<br>lorem ipsm, lorem ipsm 10250</li>
    </ul>
  </div>
</footer>
<div class="section bottom-bar">
  <span class="left">Sitemap &nbsp;|&nbsp; Privacy &amp; policy</span>
  <span class="right">Copyright 2014 Vale Linebacker All rights reserved.</span>
</div>

</body>
</html>
```